Stylish Business Cards Wanted

- DOUBLE SIDED Design Required -

High end, edgy cards for a corporate and personal stylist. Must include logo,
Name: Belinda Harwick
Title: Director and Stylist
telephone : +61 8 7142 5809
email: belinda@theloombriefing.example
website: theloombriefing.example
Tag: Corporate Workwear & Uniform Specialist | Personal Stylist
Would like nice icons for telephone, email, website

Target Market(s)

Businesses wanting stylish uniforms, people wanting stylish wardrobes

Industry/Entity Type

Corporate Workwear Stylist

Contact Information for Business Card

I would like black, white and gold foiling incorporated in the design - possibly a touch of the other colours on my branding guide attached Name: Belinda Harwick Title: Director and Stylist telephone : +61 8 7142 5809 email: belinda@theloombriefing.example website: theloombriefing.example Tag: Corporate Workwear & Uniform Specialist | Personal Stylist Would like nice icons for telephone, email, website

Font styles to use
Other font styles liked:
• Raleway

Colors

Designer to choose colors to be used in the design.

Requirements
Must have
• Gold foil accents

```html
<!DOCTYPE html>
<html lang="en">
<head>
<meta charset="UTF-8">
<title>The Loom Briefing — Business Cards</title>
<link rel="stylesheet" href="https://fonts.googleapis.com/css2?family=Open+Sans:wght@400;600;700&display=swap">
<style>
  :root {
    --backdrop: #2a2a2c;
    --card-black: #161616;
    --card-white: #fbfbfa;
    --gold: #c9a646;
    --gold-soft: #b89a52;
    --ink: #2b2b2b;
  }
  * { margin: 0; padding: 0; box-sizing: border-box; }
  html, body {
    width: 1200px; height: 900px; overflow: hidden;
    background: var(--backdrop);
    font-family: "Open Sans", Arial, sans-serif;
  }
  .canvas { position: relative; width: 1200px; height: 900px; }

  .card {
    position: absolute; left: 280px;
    width: 640px; height: 366px;
    box-shadow: 0 18px 40px rgba(0,0,0,.45);
  }
  .card--front { top: 64px; background: var(--card-black); }
  .card--back { top: 470px; background: var(--card-white); }

  /* Brand name set as plain text */
  .brand-name {
    font-weight: 700; letter-spacing: .02em; white-space: nowrap;
  }
  .card--front .brand {
    position: absolute; left: 0; right: 0; top: 118px;
    display: flex; justify-content: center; align-items: center; gap: 16px;
  }
  .card--front .brand-mark { width: 18px; height: 18px; background: var(--gold); }
  .card--front .brand-name { font-size: 46px; color: var(--gold); }

  .tagline {
    position: absolute; left: 0; right: 0; bottom: 44px;
    text-align: center; font-size: 15px; color: var(--gold-soft); letter-spacing: .02em;
  }
  .tagline .dot { margin: 0 10px; }

  .card--back .brand {
    position: absolute; left: 44px; top: 78px;
    display: flex; align-items: center; gap: 12px;
  }
  .card--back .brand-mark { width: 14px; height: 14px; background: var(--ink); }
  .card--back .brand-name { font-size: 30px; color: var(--ink); }

  .person {
    position: absolute; right: 44px; top: 112px; text-align: right;
  }
  .person-name {
    font-size: 22px; font-weight: 700; color: var(--gold);
    text-transform: uppercase; letter-spacing: .02em;
  }
  .person-title { font-size: 15px; color: var(--ink); margin-top: 2px; }

  .rule { position: absolute; height: 1px; background: var(--gold); }
  .rule--name { right: 44px; top: 186px; width: 300px; }
  .rule--contact { left: 44px; top: 236px; width: 330px; }

  .contacts {
    position: absolute; left: 44px; top: 252px; list-style: none;
  }
  .contacts li {
    display: flex; align-items: center; gap: 10px;
    font-size: 15px; color: var(--ink); line-height: 26px;
  }
  .contacts svg { width: 14px; height: 14px; fill: var(--gold); flex: none; }
</style>
</head>
<body>
<main class="canvas">

  <section class="card card--front" aria-label="Business card front">
    <div class="brand">
      <span class="brand-mark"></span>
      <span class="brand-name">The Loom Briefing</span>
    </div>
    <p class="tagline">Corporate Workwear &amp; Uniform Specialist<span class="dot">•</span>Personal Stylist</p>
  </section>

  <section class="card card--back" aria-label="Business card back">
    <div class="brand">
      <span class="brand-mark"></span>
      <span class="brand-name">The Loom Briefing</span>
    </div>

    <div class="person">
      <p class="person-name">Belinda Harwick</p>
      <p class="person-title">Director and Stylist</p>
    </div>
    <div class="rule rule--name"></div>
    <div class="rule rule--contact"></div>

    <ul class="contacts">
      <li>
        <svg viewBox="0 0 24 24" aria-hidden="true"><path d="M6.6 10.8a15.1 15.1 0 0 0 6.6 6.6l2.2-2.2a1 1 0 0 1 1-.25 11.4 11.4 0 0 0 3.6.57 1 1 0 0 1 1 1V20a1 1 0 0 1-1 1A17 17 0 0 1 3 4a1 1 0 0 1 1-1h3.5a1 1 0 0 1 1 1c0 1.25.2 2.45.57 3.57a1 1 0 0 1-.25 1z"/></svg>
        +61 8 7142 5809
      </li>
      <li>
        <svg viewBox="0 0 24 24" aria-hidden="true"><path d="M2 5h20v14H2z M4 7v.4l8 5 8-5V7l-8 5z" fill-rule="evenodd"/></svg>
        belinda@theloombriefing.example
      </li>
      <li>
        <svg viewBox="0 0 24 24" aria-hidden="true"><path d="M12 2a10 10 0 1 0 0 20 10 10 0 0 0 0-20zm0 2c.9 1.2 1.6 2.8 1.9 5h-3.8c.3-2.2 1-3.8 1.9-5zM4.3 13a8 8 0 0 1 0-2h3.8a17 17 0 0 0 0 2zm.6 2h3.4c.3 1.6.8 3 1.4 4.1A8 8 0 0 1 4.9 15zm3.4-6H4.9a8 8 0 0 1 4.8-4.1C9.1 6 8.6 7.4 8.3 9zM12 20c-.9-1.2-1.6-2.8-1.9-5h3.8c-.3 2.2-1 3.8-1.9 5zm2.1-7h-4.2a15 15 0 0 1 0-2h4.2a15 15 0 0 1 0 2zm.2 6.1c.6-1.1 1.1-2.5 1.4-4.1h3.4a8 8 0 0 1-4.8 4.1zM15.9 13a17 17 0 0 0 0-2h3.8a8 8 0 0 1 0 2zm-.2-4c-.3-1.6-.8-3-1.4-4.1A8 8 0 0 1 19.1 9z"/></svg>
        theloombriefing.example
      </li>
    </ul>
  </section>

</main>
</body>
</html>
```